Brand new letterhead, business card, email signature etc.

We are a financial company in London, UK. Our website is www.marlowvane.com. We're wanting a complete remodel of the company colours, letter head, business cards, email signatures, etc. Looking to keep the same font for the company name. I have upload a colour palette that we want to work with. We're looking for company letterhead for outgoing letters/ correspondence, letterhead for internal documentation, email signatures, e-letters. etc. Ultimately we will redesign the entire website also. It is important that our clients get a strong, secure, warm, trustworthy, solid feeling and first impression.
Updates

Designs look the same

Target Market(s)

Institutional investors, (ultra) high net worth individuals

Industry/Entity Type

Finance, Invesments banking.

Font styles to use
Other font styles liked:
• Current font is "Champagne & Limousines"

Requirements
Must have
• Must use the colours provided on the PDF uploaded to the portal. The purple = main colour. The red = accent colour.
Nice to have
• Nice to use same font as now for the company name "Corvane". Font is "Champagne & Limousines". Nice to have some reference to the old logo flower, but only subtle.
Should not have
• Do not use the colour red from our website. Use the colours provided on the colour palette PDF that I uploaded in the portal.

```html
<!DOCTYPE html>
<html lang="en">
<head>
<meta charset="utf-8">
<title>Corvane Letterhead</title>
<link href="https://fonts.googleapis.com/css2?family=Open+Sans:wght@400;600&family=Raleway:wght@300;600&display=swap" rel="stylesheet">
<style>
  :root {
    --plum: #47343f;
    --coral: #d0564a;
    --paper: #ebebeb;
    --backdrop: #d8d5d2;
    --ink-strong: #545454;
    --ink: #7c7c7c;
    --footer-ink: #f2eef0;
  }
  * { margin: 0; padding: 0; box-sizing: border-box; }
  html, body { width: 1200px; height: 1200px; overflow: hidden; }
  body { background: var(--backdrop); font-family: "Open Sans", sans-serif; }

  .letterhead {
    position: absolute; left: 147px; top: 14px;
    width: 906px; height: 1172px;
    background: var(--paper);
    box-shadow: 0 6px 22px rgba(0,0,0,0.18);
  }

  .header-band-left { position: absolute; left: 0; top: 46px; width: 130px; height: 45px; background: var(--plum); }
  .header-band-right { position: absolute; left: 346px; top: 46px; width: 560px; height: 45px; background: var(--coral); }
  .brand { position: absolute; left: 142px; top: 44px; width: 198px; height: 50px; display: flex; align-items: center; gap: 9px; z-index: 1; }
  .brand-square { flex: none; width: 46px; height: 46px; border: 1px solid var(--ink-strong); }
  .brand-name {
    font-family: "Raleway", sans-serif; font-weight: 300;
    font-size: 22px; letter-spacing: 3px; color: var(--ink-strong);
    white-space: nowrap;
  }

  .sender { position: absolute; left: 157px; top: 208px; }
  .sender-name { font-weight: 600; font-size: 18px; color: var(--ink-strong); margin-bottom: 9px; }
  .sender-line { font-size: 11.5px; line-height: 18px; color: var(--ink); }
  .letter-date { position: absolute; right: 163px; top: 290px; font-size: 11.5px; color: var(--ink); }

  .letter-body { position: absolute; left: 157px; top: 351px; width: 586px; }
  .letter-body p {
    font-size: 11.3px; line-height: 18px; color: var(--ink);
    text-align: justify; margin-bottom: 18px;
  }

  .signature { position: absolute; left: 157px; top: 811px; }
  .signature-mark { width: 140px; height: 30px; background: linear-gradient(90deg, #cfcfcf, #dedede); margin-bottom: 6px; }
  .signatory-name { font-family: "Raleway", sans-serif; font-weight: 600; font-size: 16px; color: var(--ink-strong); }
  .signatory-role { font-size: 11.5px; color: var(--ink); margin-top: 3px; }

  .footer-band { position: absolute; left: 0; top: 1089px; width: 906px; height: 60px; background: var(--plum); color: var(--footer-ink); font-size: 10.5px; }
  .footer-accent { position: absolute; left: 0; top: 1149px; width: 906px; height: 23px; background: var(--coral); }
  .contact-row { position: absolute; left: 0; width: 100%; display: flex; justify-content: center; gap: 26px; }
  .contact-row.primary { top: 11px; }
  .contact-row.secondary { top: 36px; }
  .contact-item { display: flex; align-items: center; gap: 8px; white-space: nowrap; }
  .contact-item svg { width: 14px; height: 14px; fill: var(--coral); }
</style>
</head>
<body>
<main class="letterhead">
  <div class="header-band-left"></div>
  <div class="header-band-right"></div>
  <div class="brand">
    <div class="brand-square"></div>
    <span class="brand-name">CORVANE</span>
  </div>

  <section class="sender">
    <div class="sender-name">Name Surname</div>
    <div class="sender-line">Senior Executive</div>
    <div class="sender-line">Address goes here. Street, City, Country</div>
    <div class="sender-line">contact@yourmail.com</div>
    <div class="sender-line">000-987-654-321</div>
  </section>
  <div class="letter-date">Date, 10 September, 2030</div>

  <section class="letter-body">
    <p>Lorem ipsum dolor sit amet, consectetur adipisicing elit, sed do eiusmod tempor incididunt ut labore et dolore magna aliqua. Ut enim ad minim veniam, quis nostrud exercitation ullamco laboris nisi ut aliquip ex ea commodo consequat. Duis aute irure dolor in reprehenderit in voluptate velit esse cillum dolore eu fugiat nulla pariatur. Excepteur sint occaecat cupidatat non proident, sunt in culpa qui officia deserunt mollit anim id est laborum. Sed ut perspiciatis unde omnis iste natus error sit voluptatem accusantium doloremque laudantium, totam rem aperiam, eaque ipsa quae ab illo inventore veritatis et quasi architecto beatae vitae dicta sunt explicabo. Nemo enim ipsam voluptatem quia voluptas sit aspernatur aut odit aut fugit, sed quia consequuntur magni dolores eos qui ratione voluptatem sequi nesciunt. Neque porro voluptatem sequi nesciunt. Nemo enim ipsam voluptatem quia voluptas.</p>
    <p>Lorem ipsum dolor sit amet, consectetur adipisicing elit, sed do eiusmod tempor incididunt ut labore et dolore magna aliqua. Ut enim ad minim veniam, quis nostrud exercitation ullamco laboris nisi ut aliquip ex ea commodo consequat. Duis aute irure dolor in reprehenderit in voluptate velit esse cillum dolore eu fugiat nulla pariatur. Excepteur sint occaecat cupidatat non proident, sunt in culpa qui officia deserunt mollit anim id est laborum. Sed ut perspiciatis unde omnis iste natus error sit voluptatem accusantium doloremque laudantium, totam rem aperiam, eaque ipsa quae ab illo inventore veritatis et quasi architecto beatae vitae dicta sunt explicabo. Nemo enim ipsam voluptatem quia voluptas sit aspernatur aut odit aut.</p>
    <p>Lorem ipsum dolor sit amet, consectetur adipisicing elit, sed do eiusmod tempor incididunt ut labore et dolore magna aliqua. Ut enim ad minim veniam, quis nostrud exercitation ullamco laboris nisi ut aliquip ex ea commodo consequat. .</p>
  </section>

  <section class="signature">
    <div class="signature-mark" role="img" aria-label="Handwritten signature of the sender"></div>
    <div class="signatory-name">NAME SURNAME</div>
    <div class="signatory-role">General Manager</div>
  </section>

  <footer class="footer-band">
    <div class="contact-row primary">
      <span class="contact-item">
        <svg viewBox="0 0 16 16"><path d="M1 6c0-2 3-3 7-3s7 1 7 3v1h-4V5.5H5V7H1z"/><path d="M4 8h8l2 6H2z"/></svg>
        +44 20 7946 0182
      </span>
      <span class="contact-item">
        <svg viewBox="0 0 16 16"><path d="M1 2l14 6-14 6 3-6z"/></svg>
        info@corvane.com
      </span>
      <span class="contact-item">
        <svg viewBox="0 0 16 16"><circle cx="8" cy="8" r="7"/><path d="M5 5l3 1 2-2 1 4-3 3-2-2z" fill="#47343f"/></svg>
        www.marlowvane.com
      </span>
    </div>
    <div class="contact-row secondary">
      <span class="contact-item">
        <svg viewBox="0 0 16 16"><path d="M8 1a5 5 0 0 1 5 5c0 4-5 9-5 9S3 10 3 6a5 5 0 0 1 5-5z"/><circle cx="8" cy="6" r="2" fill="#47343f"/></svg>
        Corvane Group Limited, 8th Floor, 14 Aldgate Row, London, EC3N 2LP
      </span>
    </div>
  </footer>
  <div class="footer-accent"></div>
</main>
</body>
</html>
```